Flat bootstrap design for existing site

I'm looking for a modern flat design based around an existing logo. This has to be a custom design (no external templates), and implemented into a bootstrap framework.

The logo is attached as 2 versions - choose whichever you want, that flows better with whatever design you choose.

Added screenshots of the existing site (currently using the default bootstrap layouts). Please make your designs around those pages in the screenshots (i.e. the homepage only has the postal code input and the header). The active page has 3 screenshots, because I wanted to illustrate the other states that would be visible (in the table rows).

This is a moving/junk removal website, just for some context.

Here's some example websites (flat designs) that I like, just to give you an idea of what I'm after.

https://www.plimvora.com/
https://dacklow.com/
https://trevanu.com/
https://quobrintal.com/en/

Coding

Coded - Design and coding required

Number of Pages Required

5+ page

Colors

Designer to choose colors to be used in the design.

Requirements
Must have
• It must be a modern/simple flat design, that is built around the existing logo (attached).
• It has to be implemented using bootstrap.

```html
<!DOCTYPE html>
<html lang="en">
<head>
<meta charset="utf-8">
<title>Haulora – Sign In</title>
<link rel="stylesheet" href="https://fonts.googleapis.com/css2?family=Open+Sans:wght@400;600;700&display=swap">
<style>
  :root {
    --sky: #4ac9f5;
    --sky-deep: #41b4dc;
    --white: #ffffff;
    --panel: #f3f3f3;
    --panel-border: #d9d9d9;
    --field-border: #d6d6d6;
    --ink: #2a2a2a;
    --field-ink: #1a1a1a;
  }
  * { box-sizing: border-box; margin: 0; padding: 0; }
  html, body {
    width: 1200px;
    height: 568px;
    overflow: hidden;
    background: var(--white);
    font-family: "Open Sans", Arial, sans-serif;
  }
  .site-header {
    position: relative;
    height: 81px;
    background: var(--sky);
  }
  .brand {
    position: absolute;
    left: 99px;
    top: 0;
    height: 81px;
    display: flex;
    align-items: center;
    gap: 8px;
    color: var(--white);
    font-weight: 700;
    font-size: 30px;
    letter-spacing: 1px;
    text-decoration: none;
  }
  .brand-dot {
    width: 14px;
    height: 14px;
    border-radius: 50%;
    background: var(--white);
  }
  .main-nav {
    position: absolute;
    right: 72px;
    top: 0;
    height: 81px;
    display: flex;
  }
  .main-nav a {
    display: flex;
    align-items: center;
    height: 81px;
    padding: 0 27px;
    color: var(--white);
    font-weight: 700;
    font-size: 15px;
    text-decoration: none;
    text-transform: uppercase;
  }
  .main-nav a.is-active { background: var(--sky-deep); }
  .signin-panel {
    position: absolute;
    left: 99px;
    top: 163px;
    width: 1001px;
    height: 304px;
    background: var(--panel);
    border: 2px solid var(--panel-border);
    border-radius: 4px;
  }
  .signin-title {
    position: absolute;
    left: 0;
    right: 0;
    top: 42px;
    text-align: center;
    color: var(--ink);
    font-size: 26px;
    font-weight: 700;
    text-transform: uppercase;
  }
  .signin-form {
    position: absolute;
    left: 351px;
    top: 111px;
    width: 296px;
    display: flex;
    flex-direction: column;
    align-items: center;
  }
  .field {
    width: 296px;
    height: 38px;
    margin-bottom: 13px;
    padding: 0 12px;
    border: 2px solid var(--field-border);
    border-radius: 4px;
    background: var(--white);
    color: var(--field-ink);
    font-family: inherit;
    font-size: 14px;
  }
  .field::placeholder { color: var(--field-ink); opacity: 1; }
  .login-button {
    width: 110px;
    height: 39px;
    border: 0;
    border-radius: 4px;
    background: var(--sky);
    color: var(--white);
    font-family: inherit;
    font-size: 16px;
    font-weight: 600;
    text-transform: uppercase;
  }
</style>
</head>
<body>
  <header class="site-header">
    <a class="brand" href="#"><span class="brand-dot"></span>HAULORA</a>
    <nav class="main-nav">
      <a href="#">Book</a>
      <a href="#">How it works</a>
      <a href="#" class="is-active">Become a driver</a>
      <a href="#">Signin</a>
    </nav>
  </header>

  <main class="signin-panel">
    <h1 class="signin-title">Please sign in</h1>
    <form class="signin-form">
      <input class="field" type="email" placeholder="Email address">
      <input class="field" type="password" placeholder="Password">
      <button class="login-button" type="button">Login</button>
    </form>
  </main>
</body>
</html>
```